Yacht, Boats, Watersports company needs a redesign of business card

Hello Designers!
We are a Boat dealership company that sells fun in the water, we sell boats, Yachts, Kayaks and also yacht WaterSport toys. We are looking to redesign our business cards in to something a little bit more sophisticated. in a way that we can make better use of our company colors. I'm attaching a zipped file containing the company 3 sets of company logo which one is an horizontal another one is a vertical and also a chromed 3d logo. Also is included two set of business cards that we use and also some designs that i think it's interesting. We use PMS 2026c Orange and PMS 7687C Blue. I would like to see at least two different options with the orange as accent and also using blue as an accent color. It's really important for the business cards to have a font option and size that is legible to most people. Our current website is wwww.coralpennant.com. Please visit if you want to have a better feeling of the Boat dealership
You can send Single sided or double side options. We are now using single sided but we may be open for a double side option if we really like the design.
Target Market(s)
Marine, boat sales, yacht sales, water toys sales/
Contact Information for Business Card
Name: Dale Whitcombe
Address: 212 North Fenwick Lane,
Port Alder, FL 33019
Phone: 954-731-8842
Fax: 954:731-8843
Cell: 954-382-1490
Email: dw@coralpennant.com
Website: coralpennant.com
Requirements
Must have
- the current information of the business card provided.
logo
use the PMS Colors
Nice to have
- a touch of elegance and sophistication but simple
Should not have
- should not have any typography that is hard to read, the card should be simple but yet sophisticated.

```html
<!DOCTYPE html>
<html lang="en">
<head>
<meta charset="utf-8">
<title>Coral Pennant Business Card</title>
<link rel="stylesheet" href="https://fonts.googleapis.com/css2?family=Lato:wght@400;700;900&display=swap">
<style>
  :root {
    --page-bg: #e9e6e1;
    --navy: #0c3a63;
    --navy-deep: #092d4f;
    --blue: #1b5587;
    --orange: #d4522a;
    --orange-light: #de6a3f;
    --cream: #e8e1d6;
    --text-light: #d9dde2;
    --icon-orange: #d4552c;
  }
  * { margin: 0; padding: 0; box-sizing: border-box; }
  html, body {
    width: 1200px; height: 1047px; overflow: hidden;
    background: var(--page-bg);
    font-family: "Lato", Arial, sans-serif;
  }
  .card {
    position: absolute; left: 80px; top: 241px;
    width: 1040px; height: 565px;
    border-radius: 26px; overflow: hidden;
    background: linear-gradient(120deg, var(--blue) 0%, var(--navy) 45%, var(--navy-deep) 72%);
    box-shadow: 0 12px 30px rgba(0,0,0,0.18);
  }
  .accent-band {
    position: absolute; top: 0; right: 0; bottom: 0; width: 276px;
    background: linear-gradient(160deg, var(--orange-light), var(--orange));
  }
  .company-name {
    position: absolute; left: 63px; top: 70px;
    font-weight: 900; font-size: 26px; letter-spacing: 2px;
    color: var(--text-light); text-transform: uppercase;
  }
  .person-name {
    position: absolute; left: 63px; top: 186px;
    font-weight: 700; font-size: 38px; letter-spacing: 0.5px;
    color: var(--orange); text-transform: uppercase;
  }
  .person-title {
    position: absolute; left: 63px; top: 238px;
    font-size: 22px; color: var(--text-light);
  }
  .address {
    position: absolute; left: 63px; top: 284px;
    font-size: 22px; line-height: 30px; color: var(--text-light);
  }
  .contact-list {
    position: absolute; left: 56px; top: 362px; list-style: none;
  }
  .contact-list li {
    display: flex; align-items: center; height: 31px;
    font-size: 22px; color: var(--text-light);
  }
  .contact-list svg { width: 20px; height: 20px; margin-right: 24px; fill: var(--icon-orange); }
  .brand-seal {
    position: absolute; left: 537px; top: 56px;
    width: 454px; height: 454px; border-radius: 50%;
    background: var(--cream);
    display: flex; align-items: center; justify-content: center;
  }
  .brand-seal span {
    font-weight: 900; font-size: 44px; letter-spacing: 2px;
    color: var(--navy); text-transform: uppercase; text-align: center; line-height: 1.15;
  }
</style>
</head>
<body>
  <div class="card">
    <div class="accent-band"></div>

    <div class="company-name">Coral Pennant</div>
    <div class="person-name">Dale Whitcombe</div>
    <div class="person-title">Founder &amp; CEO</div>
    <div class="address">212 North Fenwick Lane,<br>Port Alder, FL 33019</div>

    <ul class="contact-list">
      <li><svg viewBox="0 0 20 20"><path d="M2 7c0-3 3-4 8-4s8 1 8 4l-3 1-1-2H6L5 8z M4 10h12l2 7H2z"/></svg>954-731-8842</li>
      <li><svg viewBox="0 0 20 20"><path d="M6 1h8a1 1 0 0 1 1 1v16a1 1 0 0 1-1 1H6a1 1 0 0 1-1-1V2a1 1 0 0 1 1-1zm1 3v11h6V4zm3 12.2a.9.9 0 1 0 0 1.8.9.9 0 0 0 0-1.8z"/></svg>954-382-1490</li>
      <li><svg viewBox="0 0 20 20"><path d="M5 2h10v5H5z M2 8h16v7h-3v-3H5v3H2z M6 13h8v5H6z"/></svg>954:731-8843</li>
      <li><svg viewBox="0 0 20 20"><path d="M1 4h18v12H1z"/><path d="M1 4l9 7 9-7" fill="none" stroke="#0c3a63" stroke-width="1.6"/></svg>dw@coralpennant.com</li>
      <li><svg viewBox="0 0 20 20"><circle cx="10" cy="10" r="8" fill="none" stroke="#d4552c" stroke-width="1.6"/><ellipse cx="10" cy="10" rx="3.5" ry="8" fill="none" stroke="#d4552c" stroke-width="1.4"/><path d="M2 10h16M3.5 6h13M3.5 14h13" stroke="#d4552c" stroke-width="1.2"/></svg>www.coralpennant.com</li>
    </ul>

    <div class="brand-seal"><span>Coral<br>Pennant</span></div>
  </div>
</body>
</html>
```